Wagenhof Lindner

We need a web(graphic) design for an landing page on our internet portal providing a search engine to select a rental car. The search engine is using more as 150 rental car providers to find the best price. A comprehensive filter make the selection very quick and effective.
The design should be modern and clean. E.g. this website is what we have seen looks in our opinion good: http://wheels.quorbantrelpik.com

Reason: The decision takes a bit longer

Please change size to 960 px by 1500 px. Also please provide how many photoshop layers your design includes. Thank you.

Rental Car

```html
<!DOCTYPE html>
<html lang="en">
<head>
<meta charset="utf-8">
<title>Wagenhof Lindner – Rental Car Search</title>
<link href="https://fonts.googleapis.com/css2?family=Raleway:wght@400;500;600;700;800&display=swap" rel="stylesheet">
<style>
:root{
  --navy:#13306a;
  --navy-deep:#0f2a66;
  --orange:#f7941d;
  --orange-dark:#ee7d0c;
  --grey-text:#8c8c8c;
  --white:#ffffff;
}
*{margin:0;padding:0;box-sizing:border-box}
html,body{width:1140px;height:1200px;overflow:hidden;background:var(--white);font-family:'Raleway',sans-serif;color:var(--navy)}
.page{position:relative;width:1140px;height:1200px;overflow:hidden}
.abs{position:absolute}

/* header */
.contact{left:651px;top:7px;font-size:13px;font-weight:700;color:var(--navy)}
.lang{left:816px;top:0;width:146px;height:29px;background:var(--navy);color:#fff;font-size:11.5px;padding:8px 10px;display:flex;justify-content:space-between}
.caret{width:0;height:0;border-left:4px solid transparent;border-right:4px solid transparent;border-top:4px solid currentColor;align-self:center}
.logo{left:178px;top:34px;display:flex;align-items:center;gap:10px}
.logo-mark{width:14px;height:14px;background:var(--navy);border-radius:50%}
.logo-name{font-size:20px;font-weight:700;color:#555;letter-spacing:.3px}
.logo-tag{left:283px;top:58px;font-size:10px;color:#888}
.nav{left:581px;top:56px;display:flex;font-size:13.5px;font-weight:600;color:#777}
.nav a{display:block;padding:4px 10px;margin-right:3px}
.nav a.active{border:2px solid var(--navy);color:var(--navy);font-weight:700}

/* hero */
.hero{left:0;top:103px;width:1140px;height:430px;background:linear-gradient(180deg,#6d8db6 0%,#97aac0 45%,#c9cfcf 75%,#ffffff 100%)}
.hero-title{left:499px;top:147px;font-size:25px;font-weight:700;color:#fff;text-shadow:0 1px 3px rgba(0,0,0,.3)}
.hero-big{left:499px;top:172px;font-size:47px;font-weight:800;color:#fff;text-shadow:0 2px 4px rgba(0,0,0,.3)}
.hero-text{left:501px;top:230px;width:380px;font-size:12px;font-weight:500;color:#fff;line-height:18px;text-shadow:0 1px 2px rgba(0,0,0,.4)}
.car{left:502px;top:282px;width:458px;height:250px;background:linear-gradient(180deg,#3d4148,#1b1d21)}

/* search box */
.search{left:178px;top:139px;width:294px;height:450px;background:#fbfbfb;border:1px solid #e3e3e3;box-shadow:0 0 6px rgba(0,0,0,.15)}
.h-or{font-size:23px;font-weight:800;color:var(--orange)}
.lbl{font-size:12px;font-weight:700;color:var(--navy)}
.field{background:#fff;border:1px solid #dadada;font-size:11px;color:#999;padding:0 10px;display:flex;align-items:center;justify-content:space-between}
.field .caret{color:var(--orange)}
.cal{width:15px;height:14px;background:var(--orange);border-radius:2px}
.check{left:199px;top:294px;width:12px;height:12px;border:1px solid #ccc;background:#fff;color:var(--orange);font-size:10px;line-height:10px;text-align:center}
.check-lbl{left:217px;top:293px;font-size:11px;color:#555}
.btn{left:198px;top:526px;width:251px;height:43px;background:linear-gradient(#fba530,var(--orange-dark));clip-path:polygon(0 0,100% 0,94% 50%,100% 100%,0 100%,6% 50%);color:#fff;font-size:16px;font-weight:700;display:flex;align-items:center;justify-content:center;gap:6px}

/* divider */
.divider{left:462px;top:626px;width:215px;height:1px;background:#e3e3e3}
.dots{left:561px;top:623px;display:flex;gap:3px}
.dots i{width:5px;height:5px;border-radius:50%;background:#d6d6d6;display:block}

/* features */
.feat-col{top:653px;display:flex;flex-direction:column}
.feat-h{font-size:13px;font-weight:600;color:var(--navy);line-height:18px}
.feat-p{font-size:10.5px;color:var(--grey-text);line-height:17.8px;margin-top:6px}
.feat-col .feat-h + .feat-p + .feat-h{margin-top:11px}
.more{margin-top:10px;font-size:11px;font-weight:700;color:var(--orange);display:flex;align-items:center;gap:6px}
.more i{width:11px;height:11px;border:1.5px solid var(--orange);border-radius:50%;display:block}

/* signup */
.signup{left:178px;top:834px;width:784px;height:70px;background:var(--orange)}
.signup-h{left:203px;top:849px;font-size:17px;font-weight:500;color:#fff}
.signup-s{left:203px;top:870px;font-size:13px;color:#fff}
.email{left:485px;top:850px;width:298px;height:36px;background:#fff;border:1px solid #f2c58d;font-size:11.5px;color:#999;padding:11px 11px}
.send{left:725px;top:857px;width:51px;height:22px;background:var(--orange);color:#fff;font-size:12px;font-weight:700;text-align:center;line-height:22px}
.social{top:850px;width:39px;height:36px}

/* footer */
.footer{left:0;top:945px;width:1140px;height:219px;background:var(--navy-deep)}
.f-h{top:970px;font-size:14.5px;font-weight:700;color:#fff}
.f-list{top:996px;list-style:none;font-size:11px;color:#fff;line-height:20.6px}
.support{left:782px;top:1044px;width:180px;height:89px;border:1px solid #25407a;background:#0c2560}
.sup-l{left:800px;top:1060px;font-size:9.5px;color:var(--orange)}
.sup-n{left:800px;top:1077px;font-size:18px;font-weight:700;color:#fff}
.sup-m{left:800px;top:1100px;font-size:11px;color:#fff}
.copy{left:0;top:1173px;width:1140px;text-align:center;font-size:10.5px;color:#999}
</style>
</head>
<body>
<div class="page">

  <header>
    <div class="abs contact">CONTACT: (555) 310-2790</div>
    <div class="abs lang"><span>Select your language</span><span class="caret"></span></div>
    <div class="abs logo"><span class="logo-mark"></span><span class="logo-name">WAGENHOF LINDNER</span></div>
    <div class="abs logo-tag">A search engine to select a rental car</div>
    <nav class="abs nav">
      <a class="active">Home</a><a>Rentquill Faqs</a><a>Help</a><a>My Booking</a><a>Support</a>
    </nav>
  </header>

  <section>
    <div class="abs hero" role="img" aria-label="Landscape photo of fields under a cloudy sky"></div>
    <div class="abs hero-title">GREAT CAR HIRE DEALS</div>
    <div class="abs hero-big">NO HIDDEN FEES</div>
    <p class="abs hero-text">Phasellus eget ultricies libero.Sed dolor turpis,malesuada vitae cursus a,auctor semper neque.</p>
    <div class="abs car" role="img" aria-label="Photo of a black saloon rental car"></div>

    <form class="abs search"></form>
    <div class="abs h-or" style="left:195px;top:151px">WHERE?</div>
    <div class="abs lbl" style="left:198px;top:185px">COUNTRY</div>
    <div class="abs field" style="left:198px;top:203px;width:251px;height:28px">Select your country<span class="caret"></span></div>
    <div class="abs lbl" style="left:197px;top:236px">PICK-UP</div>
    <div class="abs field" style="left:198px;top:257px;width:251px;height:28px">Type in Pickup City or Airport Code Here</div>
    <div class="abs check">✓</div>
    <div class="abs check-lbl">Return to the same location</div>
    <div class="abs h-or" style="left:195px;top:316px">WHEN?</div>
    <div class="abs lbl" style="left:198px;top:349px">PICKUP ON</div>
    <div class="abs lbl" style="left:339px;top:349px">AT</div>
    <div class="abs field" style="left:198px;top:370px;width:129px;height:28px">mm/dd/yyyy<span class="cal"></span></div>
    <div class="abs field" style="left:339px;top:370px;width:110px;height:28px">12:00AM<span class="caret"></span></div>
    <div class="abs lbl" style="left:198px;top:405px">RETURN ON</div>
    <div class="abs lbl" style="left:339px;top:405px">AT</div>
    <div class="abs field" style="left:198px;top:425px;width:129px;height:28px">mm/dd/yyyy<span class="cal"></span></div>
    <div class="abs field" style="left:339px;top:425px;width:110px;height:28px">12:00AM<span class="caret"></span></div>
    <div class="abs lbl" style="left:198px;top:460px">I STAY IN</div>
    <div class="abs lbl" style="left:339px;top:460px">DRIVER AGE</div>
    <div class="abs field" style="left:198px;top:480px;width:129px;height:28px">Select Country<span class="caret"></span></div>
    <div class="abs field" style="left:339px;top:480px;width:110px;height:28px">25+<span class="caret"></span></div>
    <div class="abs btn">
      <svg width="14" height="14" viewBox="0 0 14 14"><circle cx="5.5" cy="5.5" r="4" fill="none" stroke="#fff" stroke-width="2"/><line x1="8.5" y1="8.5" x2="13" y2="13" stroke="#fff" stroke-width="2.4"/></svg>
      SEARCH NOW
    </div>
  </section>

  <div class="abs divider"></div>
  <div class="abs dots"><i></i><i></i><i></i></div>

  <section>
    <div class="abs feat-col" style="left:178px;width:278px">
      <h3 class="feat-h">We are leading car rental agency with 300,000 Happy Customers.</h3>
      <p class="feat-p">Morbi orci ante,consectetur id vestibulum quis,suscipit eu eros. Duis non egestas dolor.Duis non volutpat leo.Aliquam nisi eros,accumsan non gravida vitae,ultrices eu eros. Phasellus sagittis mattis tristique.</p>
      <div class="more"><i></i>LEARN MORE</div>
    </div>

    <div class="abs feat-col" style="left:471px;width:250px">
      <h3 class="feat-h">◆ Cheapest price guaranteed</h3>
      <p class="feat-p">Nunc ut nibh enim,id dapibus quam.Mauris id est at diam rutrum ultricies.Vivamus et dolor velit.Nam congue blandit nulla sed tincidunt.</p>
      <h3 class="feat-h">✱ Dedicated customer support</h3>
      <p class="feat-p">Praesent tempus egestas blandit.Nunc euismod volutpat ultrices.</p>
    </div>

    <div class="abs feat-col" style="left:740px;width:222px">
      <h3 class="feat-h">↖ Zeero Booking Fees</h3>
      <p class="feat-p">Nunc ut nibh enim,id dapibus quam.Mauris id est at diam rutrum ultricies.Vivamus et dolor velit.Nam congue blandit nulla sed tincidunt. Morbi orci ante,consectetur id vestibulum quis,suscipit eu eros.</p>
    </div>
  </section>

  <section>
    <div class="abs signup"></div>
    <div class="abs signup-h">SIGN UP FOR AMAZING OFFERS</div>
    <div class="abs signup-s">exclusive access for offers and promotions</div>
    <div class="abs email">Enter your email address</div>
    <div class="abs send">SEND</div>
    <div class="abs social" style="left:804px;background:#1ea1e0" aria-label="Social link"></div>
    <div class="abs social" style="left:850px;background:#d8232a" aria-label="Social link"></div>
    <div class="abs social" style="left:895px;background:#3b5998" aria-label="Social link"></div>
  </section>

  <footer>
    <div class="abs footer"></div>
    <div class="abs f-h" style="left:178px">EXTRA STUFF</div>
    <ul class="abs f-list" style="left:179px"><li>Site Map</li><li>Campervans</li><li>Price Promise</li><li>Blog</li><li>Meet the Lindner Team</li><li>Happy Customers</li><li>Why Us?</li></ul>
    <div class="abs f-h" style="left:373px">MORE COUNTRIES</div>
    <ul class="abs f-list" style="left:373px"><li>Scotland</li><li>Northern Ireland</li><li>Germany</li><li>Spain</li><li>France</li><li>Italy</li><li>Croatia</li></ul>
    <div class="abs f-h" style="left:574px">LEAVING EUROPE</div>
    <ul class="abs f-list" style="left:574px"><li>USA Car Rental</li><li>Canada Car Rental</li><li>Australia car rental</li><li>New Zealand Car Rental</li><li>Fiji Car Rental</li><li>Autovermietung Preisvergleich</li><li>Deutschland</li></ul>
    <div class="abs f-h" style="left:782px">FUN GUIDES &amp; TIPS</div>
    <ul class="abs f-list" style="left:782px"><li>Our Content Articles</li><li>Location Guides</li></ul>
    <div class="abs support"></div>
    <div class="abs sup-l">ONLINE SUPPORT</div>
    <div class="abs sup-n">(555) 310-2790</div>
    <div class="abs sup-m">sales@wagenhoflindner.com</div>
    <div class="abs copy">© Copyright Wagenhof Lindner 2014. All rights reserved</div>
  </footer>

</div>
</body>
</html>
```